Modern Banner and Window Decal Design For Law Firm Lawyer

We are looking for three modern and sophisticated banner design and window decal for our law firm.

Banner measurements/types:

1) Height: 130 cm Width: 160 cm (Outdoor banner)
2) Height: 200 cm Width: 85 cm (Pull up/retractable indoor banner)

Window Decal:
3) Height: 70cm width 70cm

Our law firm is based in Melbourne, Australia and we deal with property law mostly.

We prefer a white background with classic text in black or grey. We would also like a dash of colour so please use a green, blue or aqua colour palette that is consistent with our logo. Vector attached. A nice photo of property, Melbourne city viee, or family home would be nice.

We do not want any law related images - scales of justice, gavel or the like.

Our ultimate goal is to communicate that the firm is modern, professional and knowledgeable

We would like the following:

1. Our logo
2. Our services: - Property Law - Wills - Powers of Attorney - Probate - Estate Administration - Consultancy & Agency
3. Phone number
4. Web Address

5. For pull up/retractable banner we would also like the following text:

We use the latest digital technology and fixed-fees to provide fast and affordable legal advice that is easy to understand.

For privacy reasons, we will provide business details once we have decided on the winner.

We will monitor entries closely and promise to provide feedback and guidance on each entry.

Thank you very much for considering this project.

Target Market(s)

General public, professionals, lawyers and conveyancers

Industry/Entity Type

Law Firm

Font styles to use
Sans Serif

Colors
0393ce
34a6d7
0456a4
3176b5
acd037
33b8a4
86cfc6
00a990
9ccb3b

Requirements
Must have
• 1. Our logo
• 2. Our services: - Property Law - Wills - Powers of Attorney - Probate & Estate Administration - Consultancy & Agency
• 3. Phone number
• 4. Web Address
Nice to have
• Picture of Melbourne, Australia city ; property/buildings/lawyers
Should not have
• We do not want any law related images - scales of justice, gavel or the like.

```html
<!DOCTYPE html>
<html lang="en">
<head>
<meta charset="utf-8">
<title>Ridgeway Legal – Pull-up Banner</title>
<link rel="stylesheet" href="https://fonts.googleapis.com/css2?family=Montserrat:wght@500;600;700&family=Roboto+Condensed:wght@400;700&display=swap">
<style>
  :root {
    --page-bg: #dcdde0;
    --white: #ffffff;
    --sky-tint: #e6f2fb;
    --brand-blue: #0393ce;
    --brand-light: #34a6d7;
    --brand-deep: #0456a4;
    --brand-mid: #3176b5;
    --brand-aqua: #33b8a4;
    --ink: #111111;
    --grey-text: #555a60;
  }
  * { box-sizing: border-box; margin: 0; padding: 0; }
  html, body {
    width: 1200px; height: 1000px; overflow: hidden;
    background: var(--page-bg);
  }
  .banner {
    position: absolute; left: 350px; top: 35px;
    width: 500px; height: 930px;
    background: linear-gradient(to bottom, var(--white) 0%, var(--sky-tint) 25%, #f3f8fc 36%);
    overflow: hidden;
    box-shadow: 0 6px 18px rgba(0,0,0,0.25);
    font-family: "Montserrat", Arial, sans-serif;
  }
  .layer { position: absolute; left: 0; width: 500px; }
  .header-shape { top: 0; height: 190px; }
  .brand {
    position: absolute; top: 48px; left: 60px;
    display: flex; align-items: center; gap: 16px;
  }
  .brand-dot {
    width: 74px; height: 74px; border-radius: 50%;
    background: var(--brand-light);
  }
  .brand-name {
    font-weight: 500; font-size: 26px; line-height: 1.05;
    letter-spacing: 1px; color: var(--grey-text);
  }
  .services {
    position: absolute; top: 197px; left: 0; width: 500px;
  }
  .services-title {
    display: block; width: 146px; margin: 0 auto 10px;
    background: var(--brand-deep); color: var(--white);
    font-weight: 600; font-size: 16px; text-align: center;
    border-radius: 6px; padding: 2px 0 1px;
  }
  .service-list {
    list-style: none; padding-left: 22px;
    font-weight: 700; font-size: 16px; color: var(--ink);
  }
  .service-list li { height: 26px; line-height: 26px; }
  .service-list li::before {
    content: ""; display: inline-block; width: 7px; height: 7px;
    background: var(--brand-mid); margin-right: 5px; vertical-align: 2px;
  }
  .service-list .pair { display: flex; gap: 40px; }
  .service-list .pair span::before {
    content: ""; display: inline-block; width: 7px; height: 7px;
    background: var(--brand-mid); margin-right: 5px; vertical-align: 2px;
  }
  .service-list li.pair::before { display: none; }
  .photo {
    top: 335px; height: 470px;
    background: linear-gradient(to bottom,
      #eef6fb 0%, #e3dccd 14%, #cdbb9c 32%, #a98a6a 50%,
      #7e6a55 62%, #6b8b3c 78%, #5f8535 100%);
  }
  .footer-shape { top: 735px; height: 195px; }
  .tagline {
    position: absolute; top: 808px; left: 38px; width: 302px;
    border: 1px solid var(--brand-mid); border-radius: 4px;
    padding: 4px 6px; background: var(--white);
    font-family: "Roboto Condensed", Arial, sans-serif;
    font-size: 12px; line-height: 1.3; text-align: center; color: var(--ink);
    width: 424px;
  }
  .contact {
    position: absolute; top: 855px; left: 0; width: 500px; text-align: center;
    font-family: "Roboto Condensed", Arial, sans-serif; color: var(--ink);
  }
  .phone {
    display: inline-flex; align-items: center; gap: 8px;
    font-weight: 700; font-size: 30px; line-height: 1;
  }
  .phone-icon { width: 26px; height: 26px; }
  .web { display: block; margin-top: 6px; font-size: 17px; }
  .web strong { font-weight: 700; }
</style>
</head>
<body>
  <main class="banner">
    <svg class="layer header-shape" viewBox="0 0 500 190" aria-hidden="true">
      <path d="M0 0 H500 V108 C390 158 220 182 0 152 Z" fill="#ffffff"/>
      <path d="M0 152 C220 182 390 158 500 108 L500 122 C380 178 200 196 0 176 Z" fill="#34a6d7"/>
    </svg>

    <div class="brand">
      <span class="brand-dot"></span>
      <span class="brand-name">RIDGEWAY<br>LEGAL</span>
    </div>

    <section class="services">
      <span class="services-title">OUR SERVICES:</span>
      <ul class="service-list">
        <li class="pair"><span>PROPERTY LAW</span><span>WILLS</span></li>
        <li>POWERS OF ATTORNEY</li>
        <li>PROBATE &amp; ESTATE ADMINISTRATION</li>
        <li>CONSULTANCY &amp; AGENCY</li>
      </ul>
    </section>

    <div class="layer photo" role="img" aria-label="Photo of a smiling family of four standing on the lawn in front of their suburban family home"></div>

    <svg class="layer footer-shape" viewBox="0 0 500 195" aria-hidden="true">
      <path d="M0 70 C140 25 330 10 500 12 V195 H0 Z" fill="#34a6d7"/>
      <path d="M0 84 C140 40 330 22 500 24 V195 H0 Z" fill="#ffffff"/>
    </svg>

    <p class="tagline">We use the latest digital technology and fixed-fees to provide fast and affordable legal advice that is easy to understand.</p>

    <div class="contact">
      <span class="phone">
        <svg class="phone-icon" viewBox="0 0 26 26" aria-hidden="true">
          <rect width="26" height="26" rx="5" fill="#0456a4"/>
          <path d="M8.5 5.5c.6-.3 1.3-.1 1.6.5l1.3 2.6c.3.6.1 1.2-.4 1.6l-1.1.8c.8 1.9 2.2 3.4 4.1 4.2l.8-1.1c.4-.5 1-.7 1.6-.4l2.6 1.3c.6.3.8 1 .5 1.6l-.9 1.7c-.4.7-1.2 1.1-2 .9C10.9 18.2 7.8 15.1 6.6 9.9c-.2-.8.2-1.6.9-2z" fill="#ffffff"/>
        </svg>
        555-0142-7788
      </span>
      <span class="web">www.<strong>ridgewaylegal</strong>.com</span>
    </div>
  </main>
</body>
</html>
```